Elegant and modern Wedding Photography brochure

My existing brochure (attached) needs a major facelift. This is one of the main selling tools - it gets emailed to my clients when they make an equiry on what packages i offer and it is printed out and walked through at our first meeting. This brochure is as critical as my website - it needs to sing!

I'm looking for an eye-catching design that says:
Elegant
Modern
Clean
Crisp
Not cutesy or lovey-dovey thanks - we are more sophisticated and professional than that.

Update images to some of the latest weddings I've shot also. Let me know files and resolution you need. I've enabled right-click to download images on my site for a limited time. Please note that I retain copyright and will pursue any breeches.

Http://www.sarahkelbrin.com/Melbourne-wedding-photography
Updates

Thanks for all of your designs! Will take a few days to decide.

Target Market(s)

Australian Women aged 24-44

Industry/Entity Type

Wedding

Font styles to use
Other font styles liked:
• Century Gothic

Requirements
Must have
• Easy to print - does not have to be 6 A4 pages like the existing brochure
Nice to have
• Some full page images - The photos are supposed to be the hero here :-)
Should not have
• Not cutesy or lovey-dovey thanks - we are more sophisticated and professional than that.

No black backgrounds, I prefer a white thanks

No images in organic shaped boxes (like the rectangles in the logo - no thanks).
Keep the lines straight and sharp

```html
<!DOCTYPE html>
<html lang="en">
<head>
<meta charset="utf-8">
<title>Clara Vantell – Wedding Photography Brochure</title>
<link rel="stylesheet" href="https://fonts.googleapis.com/css2?family=Questrial&display=swap">
<style>
  :root {
    --backdrop: #ecebe9;
    --paper: #fdfbfb;
    --plum: #8c1b82;
    --plum-soft: #a3479d;
    --ink: #555555;
    --spine: #9b4a98;
    --photo-green: #6f7a4e;
    --photo-olive: #9aa06a;
    --photo-ivory: #e9e3dc;
    --photo-grey-dark: #3d3d3d;
    --photo-grey-light: #b9b9b9;
  }
  * { box-sizing: border-box; margin: 0; padding: 0; }
  html, body { width: 1200px; height: 900px; overflow: hidden; }
  body {
    background: var(--backdrop);
    font-family: "Questrial", "Century Gothic", sans-serif;
    color: var(--ink);
    position: relative;
  }
  .page {
    position: absolute;
    top: 58px;
    height: 794px;
    background: var(--paper);
    box-shadow: 0 1px 4px rgba(0,0,0,0.18);
  }
  .page--left { left: 40px; width: 555px; }
  .page--right { left: 595px; width: 560px; }
  .spine {
    position: absolute; left: 0; top: 0; width: 12px; height: 100%;
    background: var(--spine);
  }
  .photo { position: absolute; }
  .photo--couple-trees {
    left: 0; top: 0; width: 332px; height: 192px;
    background: linear-gradient(135deg, var(--photo-olive), var(--photo-green) 55%, var(--photo-ivory) 56%, var(--photo-green));
  }
  .photo--bride-portrait {
    left: 333px; top: 0; width: 222px; height: 192px;
    background: linear-gradient(160deg, var(--photo-olive), var(--photo-ivory) 70%);
  }
  .photo--couple-mono {
    left: 12px; top: 192px; width: 548px; height: 364px;
    background: linear-gradient(120deg, var(--photo-grey-light), var(--photo-grey-dark) 45%, var(--photo-ivory) 75%, var(--photo-grey-light));
  }
  .heading {
    color: var(--plum);
    font-weight: 400;
    position: absolute;
    white-space: nowrap;
  }
  .heading--fees {
    left: 48px; top: 232px;
    font-size: 32.5px; line-height: 29px;
  }
  .heading--remember {
    left: 47px; top: 128px;
    font-size: 31.8px; line-height: 28px;
    text-transform: uppercase;
    letter-spacing: 0.3px;
  }
  .heading--special {
    left: 171px; top: 503px;
    font-size: 35px; line-height: 36px;
    text-transform: uppercase;
  }
  .fee-list {
    position: absolute; left: 53px; top: 335px;
    list-style: none;
    font-size: 12px; line-height: 17.4px;
    white-space: nowrap;
  }
  .fee-list li { margin-bottom: 2.2px; }
  .fee-name { color: var(--plum-soft); text-transform: uppercase; }
  .page-number {
    position: absolute; top: 758px;
    font-size: 12px; color: var(--plum);
  }
  .page--left .page-number { left: 275px; }
  .page--right .page-number { left: 274px; }
  .brand {
    position: absolute; left: 206px; top: 40px;
    display: flex; align-items: center; gap: 7px;
    color: var(--plum); font-size: 19px;
  }
  .brand-mark {
    width: 28px; height: 28px;
    border: 2px solid var(--plum);
  }
  .intro {
    position: absolute; left: 47px; top: 598px; width: 470px;
    font-size: 12.4px; line-height: 17.5px;
  }
  .intro p + p { margin-top: 17.5px; }
  .intro .highlight { color: var(--plum-soft); }
</style>
</head>
<body>

<section class="page page--left">
  <div class="photo photo--couple-trees" role="img" aria-label="Bride and groom embracing beneath willow trees"></div>
  <div class="photo photo--bride-portrait" role="img" aria-label="Close portrait of a smiling bride in her veil"></div>

  <h1 class="heading heading--fees">À la carte<br>Fees to consider</h1>

  <ul class="fee-list">
    <li><span class="fee-name">Engagement session/pre-wedding shoot</span><br>$290 for up to 2 hours of photography on location</li>
    <li><span class="fee-name">Digital negatives</span> $490</li>
    <li><span class="fee-name">Extended coverage</span> $160 per hour</li>
    <li><span class="fee-name">Web gallery &amp; Snapgrid posting</span> $160</li>
    <li><span class="fee-name">Slideshow</span> $250</li>
    <li><span class="fee-name">Second photographer</span> $590</li>
    <li><span class="fee-name">Client for life</span><br>No sitting fees for portrait sessions –<br>Anniversaries, family portraits, etc: $390</li>
    <li><span class="fee-name">Photo enlargements</span><br>- Quality custom archival prints in a variety of sizes 5x7 up to 8x10<br>$25, 12.5x18.5 $50<br>- Stretched Canvas Prints for your wall Various sizes available from<br>16”x20” starting at $395 through to 60”x96” $1500<br>Plus many other options!</li>
    <li><span class="fee-name">Professionally edited album (regular)</span> $790</li>
    <li><span class="fee-name">Album upgrade from regular to signature grand</span><br>- From Gold Package to Signature Grand: $1150<br>- From Platinum Package to Signature Grand: $650</li>
    <li><span class="fee-name">Custom thank-you cards</span><br>$150 for 50 cards (174mm x 123mm) including envelopes</li>
  </ul>

  <span class="page-number">6</span>
</section>

<section class="page page--right">
  <div class="spine"></div>

  <div class="brand">
    <span class="brand-mark"></span>
    <span class="brand-name">Clara Vantell</span>
  </div>

  <h2 class="heading heading--remember">How do you want<br>to remember...</h2>

  <div class="photo photo--couple-mono" role="img" aria-label="Black and white portrait of the smiling bride and groom"></div>
  <h2 class="heading heading--special">Your special day?</h2>

  <div class="intro">
    <p>Elegant, stunning, fuss-free photography that doesn’t cost the earth will capture those memories for a lifetime!<br>
    Wedding photography packages start from $1650 and are fully inclusive of fun-filled creative &amp; journalistic coverage, digital negatives and professionally edited album.</p>
    <p>Contact Clara today to arrange an informal catch-up, discuss your requirements and find out more about the <span class="highlight">early booking bonus</span>!</p>
  </div>

  <span class="page-number">7</span>
</section>

</body>
</html>
```